Company brochure

I would like to redesign our existing brochure.
It shall be trifold brochure with more modern and better appealing design than the old one. I am uploading the old one. The new design shall have all all information repeated from old brochure. It could be more or less pictures. I will provide more pictures if required. The keep text is important, the font shall be more modern. Brochure size shall be trifoldt US Legal size paper 8.5" x 14". I will provide all pitures, logos etc in a original format after design concept will be established or before on request.

Industry/Entity Type

It Company

Font styles to use
Other font styles liked:
• calibri

Colors
0555a3
3176b5
85abd2
0692cd
33a6d7
85cae6
1ab09a
33b8a4
87cfc6

Requirements
Nice to have
• I need all information from existing brochure such as text, customer logos, professional assos. logos to be shown in a new one. Picture could be added more.
Should not have
• No changes allowed to company letterhead. Only slight modifications allowed to company logo

```html
<!DOCTYPE html>
<html lang="en">
<head>
<meta charset="utf-8">
<title>Refrigeration Services Trifold Brochure</title>
<link rel="stylesheet" href="https://fonts.googleapis.com/css2?family=Open+Sans:wght@400;600&family=Roboto:wght@300;400&display=swap">
<style>
  :root {
    --accent: #0555a3;
    --accent-bright: #0692cd;
    --accent-teal: #1ab09a;
    --ink: #5a5a5a;
    --heading: #5e6066;
    --paper: #ffffff;
    --stage: #000000;
  }
  * { box-sizing: border-box; margin: 0; padding: 0; }
  html, body { width: 1200px; height: 1200px; overflow: hidden; background: var(--stage); }
  .stage { position: relative; width: 1200px; height: 1200px; }
  .brochure {
    position: absolute; left: 40px; top: 262px;
    width: 1060px; height: 640px;
    background: var(--paper);
    transform: scale(1.0566); transform-origin: 0 0;
    font-family: "Open Sans", Arial, sans-serif; color: var(--ink);
  }
  .abs { position: absolute; }
  .photo { position: absolute; overflow: hidden; }
  .bar { position: absolute; width: 7px; background: var(--accent-bright); }
  .display {
    font-family: "Roboto", Helvetica, sans-serif; font-weight: 300;
    color: var(--heading); font-size: 26px; line-height: 25px;
  }
  .display .hl { color: var(--accent); }
  .subhead { font-weight: 600; color: var(--accent); font-size: 13px; line-height: 16px; }
  .body { font-size: 8.6px; line-height: 10.2px; text-align: justify; }
  .body p { margin-bottom: 10px; }
  .body.ragged { text-align: left; }
  .vertical {
    position: absolute; font-family: "Roboto", Helvetica, sans-serif; font-weight: 300;
    color: var(--accent-bright); font-size: 16px; white-space: nowrap;
    transform: rotate(-90deg); transform-origin: 0 0;
  }
  .footer {
    position: absolute; left: 0; top: 623px; width: 1060px; height: 17px;
    background: var(--accent);
  }
  .footer .url {
    position: absolute; top: 3px; color: #fff; font-size: 7.5px; font-weight: 600;
  }
  .tagline { font-weight: 600; color: var(--accent); font-size: 12.5px; line-height: 15px; }
</style>
</head>
<body>
<div class="stage">
  <div class="brochure">

    <!-- Panel one -->
    <div class="photo" style="left:0;top:0;width:117px;height:130px;background:linear-gradient(160deg,#c7ccd0,#5f7a7c 55%,#2f5e5c);" role="img" aria-label="Photo of teal refrigeration compressors in a plant room"></div>
    <div class="photo" style="left:117px;top:0;width:117px;height:130px;background:linear-gradient(170deg,#e3e6e8,#a9b2b8 50%,#3d6e6c);" role="img" aria-label="Photo of large white refrigeration vessels and piping"></div>
    <div class="photo" style="left:234px;top:0;width:118px;height:130px;background:linear-gradient(180deg,#d8dde1,#9aa3a8 60%,#6c7479);" role="img" aria-label="Photo of an air handling unit inside a facility"></div>
    <span class="bar" style="left:0;top:40px;height:55px;"></span>
    <span class="bar" style="left:110px;top:30px;height:70px;"></span>
    <span class="bar" style="left:230px;top:50px;height:45px;"></span>
    <span class="bar" style="left:340px;top:40px;height:60px;width:5px;"></span>

    <h1 class="display abs" style="left:49px;top:160px;width:220px;">From Design Concept Through Execution</h1>

    <h2 class="subhead abs" style="left:49px;top:251px;">Experience</h2>
    <div class="body abs" style="left:49px;top:274px;width:186px;">
      <p>Thirty plus years in industrial, commercial, ammonia and kryon refrigeration and air conditioning.</p>
      <p>Experienced in all aspects of refrigeration projects, from design concept through execution, with the ability to cost-effectively satisfy customer requirements within aggressive time frames.</p>
    </div>

    <h2 class="subhead abs" style="left:49px;top:395px;">Major Projects Completed</h2>
    <div class="body ragged abs" style="left:49px;top:417px;width:195px;">
      <p>675 TR, 1960 HP ammonia refrigeration system for a bakery.</p>
      <p>90 TR, 400 HP kryon spiral blast freezer for meat processing plant.</p>
      <p>920 TR, 1420 HP ammonia refrigeration system for meat processing facility.</p>
      <p>1300 TR kryon chiller and glycol chiller and glycol distribution system for a dairy processing plant.</p>
      <p>An ammonia refrigeration system for 560,000 sq. ft cold storage and food distribution facility.</p>
      <p>480 ton ice production facility.</p>
      <p>375 TR, 1500 HP ice-cream plant.</p>
    </div>

    <div class="vertical" style="left:285px;top:555px;">Customer Satisfaction Is Our Ultimate Goal!</div>

    <!-- Panel two -->
    <h1 class="display abs" style="left:433px;top:35px;width:240px;"><span class="hl">24</span> hour Emergency Service</h1>
    <h2 class="subhead abs" style="left:433px;top:95px;">Service and Maintenance</h2>
    <div class="body abs" style="left:433px;top:118px;width:191px;">
      <p>24 hour Emergency Service - Ammonia and Kryon. Customized maintenance program. Troubleshooting service and repair of refrigeration and HVAC systems including all mechanical, structural, electrical and control components. Compressor rebuilding as well as vibration and oil analysis. Refrigerant conversion and recovery.</p>
      <p>Build-up ammonia and kryon refrigeration systems, packaged kryon refrigeration units, blast freezing/cooling systems, spiral and tunnel freezers, holding freezers and coolers, evaporators, glycol and water chillers, ice production machines, process.</p>
    </div>

    <div class="photo" style="left:353px;top:286px;width:201px;height:118px;background:linear-gradient(180deg,#b9cde0 0 30%,#c9ced2 30%,#8b979e);" role="img" aria-label="Photo of rooftop refrigerant piping runs"></div>
    <div class="photo" style="left:554px;top:286px;width:153px;height:118px;background:linear-gradient(180deg,#a8c3dc 0 35%,#dfe3e6 35%,#9aa4aa);" role="img" aria-label="Photo of a rooftop cooling tower"></div>
    <span class="bar" style="left:353px;top:318px;height:58px;"></span>
    <span class="bar" style="left:550px;top:318px;height:58px;"></span>
    <span class="bar" style="left:702px;top:318px;height:58px;width:5px;"></span>

    <div class="body abs" style="left:433px;top:421px;width:191px;">
      <p>Compressors, evaporative and air-cool condensers, recirculation packages, ammonia, water and glycol pumps, heat exchangers, control valves and regulators, electrical motors.</p>
      <p>Safety devices test, repair and calibration including: relief valves, leak detectors, pressure and temperature sensors, level.</p>
      <p>Packaged and split gas/electric air conditioners, heat pumps. Air handlers, exhaust fans, swamp coolers, water chillers, water towers and pumps. Exhaust and ventilation, humidification and dehumidification, clean rooms. Boilers and Boiler Piping. Refrigeration and Building Control and Automation.</p>
      <p>PLC, VFD, VSD, VAV.</p>
    </div>

    <!-- Panel three -->
    <div class="photo" style="left:707px;top:0;width:155px;height:157px;background:linear-gradient(180deg,#cfd9e0 0 25%,#c4b9a3 25%,#a59a86);" role="img" aria-label="Photo of rooftop packaged units over a city"></div>
    <div class="photo" style="left:862px;top:0;width:198px;height:157px;background:linear-gradient(170deg,#dfe2e4,#7f9296 50%,#375f63);" role="img" aria-label="Photo of compressors and pipework in an engine room"></div>
    <span class="bar" style="left:707px;top:30px;height:75px;"></span>
    <span class="bar" style="left:858px;top:30px;height:75px;"></span>
    <span class="bar" style="left:1054px;top:30px;height:75px;width:6px;"></span>

    <h2 class="subhead abs" style="left:733px;top:176px;">Engineering Services</h2>
    <div class="body abs" style="left:733px;top:199px;width:210px;">
      <p>Design ammonia and kryon systems. Build-up and packaged refrigeration systems. Liquid recirculating, flooded, and DX systems. Low and high temperature chillers. Glycol and chill water distribution systems.</p>
      <p>Energy saving and expansion projects. 3D FormSolid and DraftCore drawings. Computerized control design and implementation, PLC, VFD.</p>
      <p>Mechanical integrity surveys, seismic and hazard analysis, seismic assessment. Safety programs, PSM, RMP, CalARP, MOC, SOP. Regulatory Compliance and Professional training.</p>
    </div>

    <h1 class="display abs" style="left:733px;top:348px;width:270px;white-space:nowrap;">Free survey and quote</h1>
    <p class="tagline abs" style="left:733px;top:377px;width:265px;">on your refrigeration and air conditioning equipment needs.</p>

    <div class="vertical" style="left:1014px;top:398px;">Get A Free Quote And Survey!</div>

    <div class="photo" style="left:707px;top:422px;width:353px;height:201px;background:linear-gradient(180deg,#e4e6e8 0 35%,#9fb3c9 35%,#5a7c82 65%,#3f5f63);" role="img" aria-label="Photo of a machine room with blue piping and teal compressors"></div>

    <div class="footer">
      <span class="url" style="left:27px;">www.northfrostmech.com</span>
      <span class="url" style="left:380px;">www.northfrostmech.com</span>
      <span class="url" style="left:733px;">www.northfrostmech.com</span>
    </div>
  </div>
</div>
</body>
</html>
```